Liron Vasek Website

Website for my son who is in 7th grade in the US. This will prepare him to show people his accomplishments when applying for a job or going to college. It should have:
* A picture (or multiple pictures)
* A resume page
* A place to share your accomplishments
* Links to his other social profiles
* A contact form

Great to include:
* Internships (show some photos of it along with what you’ve learned).
* Volunteer work.
* A side hustle that you want to highlight

Website sample I like:
https://belinamorud.sitefolio-demo.com/belinamorudtavik

Target Market(s)

For jobs and colleges admissions.

Number of Pages Required

5+ page

Colors

Designer to choose colors to be used in the design.

Requirements
Must have
• * A picture (or multiple pictures)
• * A resume page
• * A place to share your accomplishments
• * Links to his other social profiles
• * A contact form
Nice to have
• Great to include:
• * Internships (show some photos of it along with what you’ve learned).
• * Volunteer work.
• * A side hustle that you want to highlight

```html
<!DOCTYPE html>
<html lang="en">
<head>
<meta charset="utf-8">
<title>Liron Vasek</title>
<link rel="stylesheet" href="https://fonts.googleapis.com/css2?family=Montserrat:wght@400;500;600;700&display=swap">
<style>
  :root {
    --red: #df111b;
    --ink: #151515;
    --white: #ffffff;
    --footer: #0b0b0b;
    --muted: #2a2a2a;
  }
  * { margin: 0; padding: 0; box-sizing: border-box; }
  html, body { width: 691px; height: 1200px; overflow: hidden; }
  body {
    position: relative;
    background: var(--white);
    font-family: "Montserrat", Arial, sans-serif;
    color: var(--ink);
  }
  .nav {
    display: flex; justify-content: center; gap: 20px;
    font-size: 9.3px; font-weight: 400; color: var(--white);
    list-style: none;
  }
  .top-bar {
    position: absolute; top: 0; left: 0; width: 691px; height: 35px;
    background: var(--red);
    display: flex; align-items: center; justify-content: center;
  }
  .site-title {
    position: absolute; top: 48px; width: 100%; text-align: center;
    font-size: 22.5px; font-weight: 700; letter-spacing: 0.2px;
  }
  .site-tagline {
    position: absolute; top: 77px; width: 100%; text-align: center;
    font-size: 8.6px; color: var(--muted);
  }
  .hero {
    position: absolute; left: 42px; top: 100px; width: 607px; height: 309px;
    background:
      linear-gradient(160deg, transparent 55%, rgba(120,70,40,0.85) 80%, rgba(60,40,30,0.9) 100%),
      linear-gradient(180deg, #d9b0c0 0%, #e8b9a8 35%, #c7848f 60%, #b9869e 100%);
  }
  .hero-title {
    position: absolute; top: 157px; width: 100%; text-align: center;
    font-size: 22.5px; font-weight: 700; color: var(--white);
  }
  .btn {
    position: absolute; height: 21px; border-radius: 11px;
    display: flex; align-items: center; justify-content: center;
    font-size: 7.8px; font-weight: 700; color: var(--white);
  }
  .btn-review { left: 216px; top: 202px; width: 94px; background: var(--red); }
  .btn-call { left: 318px; top: 202px; width: 73px; border: 1.5px solid var(--white); }
  .section-title {
    position: absolute; width: 100%; text-align: center;
    font-weight: 700; font-size: 22.5px;
  }
  .section-text {
    position: absolute; left: 68px; width: 555px; text-align: center;
    font-size: 7.7px; line-height: 16px; color: var(--ink);
  }
  .btn-more {
    position: absolute; left: 311px; top: 545px; width: 69px; height: 22px;
    border-radius: 11px; background: var(--red); color: var(--white);
    font-size: 8.4px; font-weight: 700;
    display: flex; align-items: center; justify-content: center;
  }
  .gallery {
    position: absolute; left: 42px; top: 594px; width: 607px; height: 197px;
    display: flex; gap: 1px;
  }
  .tile { position: relative; flex: 1; overflow: hidden; }
  .tile-study { background: linear-gradient(135deg, #c9ccd0 0%, #e6e8ea 50%, #9aa3ad 100%); }
  .tile-portrait { background: linear-gradient(180deg, #cfcac4 0%, #b69580 50%, #5d86c2 100%); }
  .tile-talk { background: linear-gradient(180deg, #8a6a56 0%, #6b5a52 50%, #3b3a44 100%); }
  .tile-badge {
    position: absolute; right: -4px; bottom: -44px; width: 90px; height: 90px;
    border-radius: 50%; background: var(--red);
  }
  .tile-badge svg { position: absolute; left: 26px; top: 12px; }
  .call-to-action {
    position: absolute; top: 942px; width: 100%; text-align: center;
    font-size: 11.7px; font-weight: 600; line-height: 19px;
  }
  .call-to-action em { font-style: normal; color: var(--red); }
  .signature {
    position: absolute; top: 988px; width: 100%; text-align: center;
    font-size: 12.8px; font-weight: 600; color: var(--red);
  }
  .footer {
    position: absolute; left: 0; top: 1043px; width: 691px; height: 157px;
    background: var(--footer);
  }
  .footer-name {
    position: absolute; top: 26px; width: 100%; text-align: center;
    font-size: 21.5px; font-weight: 700; color: var(--red);
  }
  .footer .nav { position: absolute; top: 69px; width: 100%; }
  .social {
    position: absolute; top: 98px; width: 100%;
    display: flex; justify-content: center; gap: 22px;
  }
  .social span { width: 9px; height: 9px; border-radius: 50%; background: var(--white); }
  .copyright {
    position: absolute; top: 122px; width: 100%; text-align: center;
    font-size: 7px; color: var(--white);
  }
  .mail-button {
    position: absolute; left: 625px; top: 97px; width: 38px; height: 38px;
    border-radius: 50%; background: var(--red);
    display: flex; align-items: center; justify-content: center;
  }
</style>
</head>
<body>
  <header class="top-bar">
    <ul class="nav">
      <li>Home</li><li>Portfolio</li><li>Resume</li><li>Achievements</li>
      <li>Social profiles</li><li>Internships</li><li>Volunteer work</li><li>Contact</li>
    </ul>
  </header>

  <h1 class="site-title">Liron Vasek</h1>
  <p class="site-tagline">7th grade in the US</p>

  <section class="hero" role="img" aria-label="Man in a suit standing on a rocky peak above a misty pink sunrise valley">
    <h2 class="hero-title">Welcome To Liron Vasek</h2>
    <span class="btn btn-review">Write a Review</span>
    <span class="btn btn-call">Call Now</span>
  </section>

  <h2 class="section-title" style="top:432px;">About Liron Vasek</h2>
  <p class="section-text" style="top:470px;">Sed ut perspiciatis unde omnis iste natus error sit voluptatem accusantium doloremque laudantium, totam rem aperiam, eaque ipsa quae ab illo inventore veritatis et quasi architecto beatae vitae dicta sunt explicabo. Nemo enim ipsam voluptatem quia voluptas sit aspernatur aut odit aut fugit, sed quia consequuntur magni dolores eos qui ratione voluptatem sequi nesciunt. Neque porro quisquam est, qui dolorem ipsum quia dolor sit amet, consectetur, adipisci velit, sed quia non numquam eius modi tempora incidunt ut labore et.</p>
  <span class="btn-more">Read More</span>

  <section class="gallery">
    <div class="tile tile-study" role="img" aria-label="Student reading a book at a library desk">
      <div class="tile-badge">
        <svg width="20" height="20" viewBox="0 0 20 20"><circle cx="10" cy="10" r="7.5" fill="none" stroke="#fff" stroke-width="2.2"/></svg>
      </div>
    </div>
    <div class="tile tile-portrait" role="img" aria-label="Smiling young man in a blue shirt">
      <div class="tile-badge">
        <svg width="20" height="20" viewBox="0 0 20 20" fill="none" stroke="#fff" stroke-width="2"><circle cx="10" cy="6" r="4.5"/><path d="M2 19v-2a5 5 0 0 1 5-5h6a5 5 0 0 1 5 5v2z"/></svg>
      </div>
    </div>
    <div class="tile tile-talk" role="img" aria-label="Audience seated listening to a speaker at a lectern">
      <div class="tile-badge">
        <svg width="22" height="20" viewBox="0 0 22 20" fill="none" stroke="#fff" stroke-width="2"><path d="M1 2v16h20"/><path d="M4 14l5-5 3 3 7-7" stroke-linejoin="round"/></svg>
      </div>
    </div>
  </section>

  <h2 class="section-title" style="top:820px;">Experience &amp; Achievements</h2>
  <p class="section-text" style="top:857px;">Sed ut perspiciatis unde omnis iste natus error sit voluptatem accusantium doloremque laudantium, totam rem aperiam, eaque ipsa quae ab illo inventore veritatis et quasi architecto beatae vitae dicta sunt explicabo. Nemo enim ipsam voluptatem quia voluptas sit aspernatur aut odit aut fugit, sed quia consequuntur magni dolores eos qui ratione voluptatem sequi nesciunt. Neque porro quisquam est, qui dolorem ipsum quia dolor sit amet, consectetur, adipisci velit, sed quia non numquam eius modi tempora incidunt ut labore et.</p>

  <p class="call-to-action">For <em>my resume</em>, samples of <em>my writing</em>, and <em>achievements</em>,<br>please locate them in the other tabs.</p>
  <p class="signature">Liron Vasek</p>

  <footer class="footer">
    <p class="footer-name">Liron Vasek</p>
    <ul class="nav">
      <li>Home</li><li>Portfolio</li><li>Resume</li><li>Achievements</li>
      <li>Social profiles</li><li>Internships</li><li>Volunteer work</li><li>Contact</li>
    </ul>
    <div class="social"><span></span><span></span><span></span><span></span><span></span><span></span></div>
    <p class="copyright">© 2019 | &nbsp;www.sitename-demo.com</p>
    <span class="mail-button">
      <svg width="15" height="12" viewBox="0 0 15 12" fill="none" stroke="#fff" stroke-width="1.6"><rect x="1" y="1" width="13" height="10" rx="2"/><path d="M1.5 2l6 4.5 6-4.5"/></svg>
    </span>
  </footer>
</body>
</html>
```